Melorix artwork for new single release

I need Melorix artwork creating to release a new single on there.

The specs are:

Ideal size: 3000 x 3000 pixels
Minimum size: 1400 x 1400 pixels
Aspect ratio: 1:1 (must be a perfect square)
File format: JPG or PNG
Color space: sRGB
File size: Max 4MB

The song is called "Was It Ever Rain?"
The artist is "Martin Hollow"

We have no images of Martin, so it really is open to imagination.

Target Market(s)

Melorix listeners

Industry/Entity Type

Music

```html
<!DOCTYPE html>
<html lang="en">
<head>
<meta charset="utf-8">
<title>Was It Ever Rain? — Martin Hollow</title>
<link rel="stylesheet" href="https://fonts.googleapis.com/css2?family=Oswald:wght@600&family=Montserrat:wght@300&display=swap">
<style>
  :root {
    --ink-black: #0d0907;
    --umber: #2a1710;
    --ember: #b8643c;
    --skin-glow: #d98a5c;
    --title-white: #ececec;
    --title-shadow: #8e8e8e;
    --shift-red: rgba(230, 40, 60, 0.75);
    --shift-cyan: rgba(40, 220, 230, 0.6);
    --artist-white: #f4f4f4;
  }
  html, body {
    margin: 0;
    padding: 0;
    width: 1200px;
    height: 1200px;
    overflow: hidden;
    background: var(--ink-black);
  }
  .cover {
    position: relative;
    width: 1200px;
    height: 1200px;
    overflow: hidden;
  }
  .cover-photo {
    position: absolute;
    inset: 0;
    display: block;
  }
  .title-block {
    position: absolute;
    left: 0;
    right: 0;
    top: 420px;
    display: flex;
    justify-content: center;
    align-items: flex-start;
    gap: 14px;
    font-family: "Oswald", "Arial Narrow", sans-serif;
    font-weight: 600;
    color: var(--title-white);
    text-transform: uppercase;
    text-shadow:
      -3px 0 0 var(--shift-red),
      3px 0 0 var(--shift-cyan),
      6px 5px 0 var(--title-shadow);
  }
  .title-lines {
    display: flex;
    flex-direction: column;
    align-items: flex-end;
    font-size: 168px;
    line-height: 184px;
    letter-spacing: 1px;
  }
  .title-mark {
    font-size: 420px;
    line-height: 360px;
    margin-top: 6px;
  }
  .artist-name {
    position: absolute;
    left: 0;
    right: 0;
    top: 968px;
    text-align: center;
    font-family: "Montserrat", "Helvetica", sans-serif;
    font-weight: 300;
    font-size: 40px;
    line-height: 40px;
    letter-spacing: 46px;
    padding-left: 46px;
    color: var(--artist-white);
    text-transform: uppercase;
  }
</style>
</head>
<body>
  <main class="cover">
    <svg class="cover-photo" width="1200" height="1200" viewBox="0 0 1200 1200" role="img" aria-label="Dark, grainy photograph of a figure with a hand raised across the face, warm amber light on skin against a near-black smoky background">
      <defs>
        <radialGradient id="warmGlow" cx="0.58" cy="0.45" r="0.55">
          <stop offset="0" stop-color="var(--skin-glow)" stop-opacity="0.75"/>
          <stop offset="0.35" stop-color="var(--ember)" stop-opacity="0.45"/>
          <stop offset="0.7" stop-color="var(--umber)" stop-opacity="0.6"/>
          <stop offset="1" stop-color="var(--ink-black)" stop-opacity="1"/>
        </radialGradient>
        <linearGradient id="floorShade" x1="0" y1="0" x2="0" y2="1">
          <stop offset="0.6" stop-color="#000" stop-opacity="0"/>
          <stop offset="1" stop-color="#000" stop-opacity="0.6"/>
        </linearGradient>
      </defs>
      <rect width="1200" height="1200" fill="var(--ink-black)"/>
      <rect width="1200" height="1200" fill="url(#warmGlow)"/>
      <rect width="1200" height="1200" fill="url(#floorShade)"/>
    </svg>

    <h1 class="title-block">
      <span class="title-lines">
        <span class="title-line">Was It Ever</span>
        <span class="title-line">Rain</span>
      </span>
      <span class="title-mark">?</span>
    </h1>

    <p class="artist-name">Martin Hollow</p>
  </main>
</body>
</html>
```